Verlindo Magician

I want the business card for my business to give to people who watch that later I will be employed to show magic here is my website http://www.verlindoillusions.example/I want the interesting design , i am very opened for formal and informal, I watch a lot of design so don't stick to the common shape and form but i hope it can also be produced the thing to write on will be the same as in picture that i will upload , i also will upload the logo for you that so can be easy to useDenis CostilleMagicianMAGICIAN VERLINDO 17 rue des Tilleuls - 25000 BESANÇON contact@verlindoillusions.example tel. 0381 946 157 tel. 0674 219 503

```html
<!DOCTYPE html>
<html lang="fr">
<head>
<meta charset="utf-8">
<title>Verlindo Magician – Business Card</title>
<link rel="stylesheet" href="https://fonts.googleapis.com/css2?family=Jost:wght@300;400&display=swap">
<style>
  :root {
    --page-bg: #e4e4e4;
    --card-bg: #f3f3f3;
    --brand-red: #c8000a;
    --ink: #2b2b2b;
    --ink-soft: #3a3a3a;
    --portrait-dark: #151515;
    --portrait-mid: #2e2e2e;
    --band-text: #ffffff;
  }
  html, body {
    margin: 0;
    padding: 0;
    width: 1200px;
    height: 900px;
    overflow: hidden;
    background: var(--page-bg);
    font-family: "Jost", sans-serif;
  }
  .card {
    position: absolute;
    left: 75px;
    top: 150px;
    width: 1050px;
    height: 600px;
    background: var(--card-bg);
    overflow: hidden;
  }
  .brand-band {
    position: absolute;
    left: 0;
    top: 54px;
    width: 100%;
    height: 103px;
    background: var(--brand-red);
  }
  .brand-name {
    position: absolute;
    left: 63px;
    top: 60px;
    margin: 0;
    font-weight: 300;
    font-size: 70px;
    line-height: 1;
    letter-spacing: 1px;
    color: var(--band-text);
  }
  .portrait {
    position: absolute;
    left: 575px;
    top: 0;
    width: 470px;
    height: 600px;
    background: linear-gradient(180deg, var(--portrait-mid) 0%, var(--portrait-dark) 100%);
  }
  .person-name {
    position: absolute;
    left: 63px;
    top: 190px;
    margin: 0;
    font-weight: 400;
    font-size: 40px;
    line-height: 1;
    color: var(--brand-red);
  }
  .person-role {
    position: absolute;
    left: 63px;
    top: 249px;
    margin: 0;
    font-weight: 300;
    font-size: 28px;
    line-height: 1;
    color: var(--ink-soft);
  }
  .company {
    position: absolute;
    left: 63px;
    top: 309px;
    margin: 0;
    font-weight: 400;
    font-size: 23px;
    line-height: 1;
    color: var(--brand-red);
  }
  .address {
    position: absolute;
    left: 63px;
    top: 339px;
    margin: 0;
    font-weight: 400;
    font-size: 23px;
    line-height: 1;
    letter-spacing: 0.5px;
    color: var(--ink);
  }
  .contact-list {
    position: absolute;
    left: 63px;
    top: 395px;
    margin: 0;
    padding: 0;
    list-style: none;
  }
  .contact-item {
    display: flex;
    align-items: center;
    height: 39.5px;
    font-weight: 400;
    font-size: 23px;
    color: var(--ink);
  }
  .contact-icon {
    width: 22px;
    height: 22px;
    margin-right: 17px;
    flex: none;
    fill: var(--brand-red);
  }
</style>
</head>
<body>
  <main class="card">
    <div class="brand-band"></div>
    <h1 class="brand-name">VERLINDO</h1>

    <div class="portrait" role="img" aria-label="Black and white illustration of the magician in a dark jacket holding a playing card"></div>

    <h2 class="person-name">MARC RAVOULET</h2>
    <p class="person-role">MAGICIAN</p>

    <p class="company">MAGICIAN VERLINDO</p>
    <p class="address">17 rue des Tilleuls - 25000 BESANÇON</p>

    <ul class="contact-list">
      <li class="contact-item">
        <svg class="contact-icon" viewBox="0 0 24 24" aria-hidden="true"><path d="M6.6 10.8a15.1 15.1 0 0 0 6.6 6.6l2.2-2.2c.3-.3.7-.4 1-.2 1.1.4 2.3.6 3.6.6.6 0 1 .4 1 1V20c0 .6-.4 1-1 1A17 17 0 0 1 3 4c0-.6.4-1 1-1h3.5c.6 0 1 .4 1 1 0 1.3.2 2.5.6 3.6.1.3 0 .7-.2 1z"/></svg>
        <span>0381 946 157</span>
      </li>
      <li class="contact-item">
        <svg class="contact-icon" viewBox="0 0 24 24" aria-hidden="true"><path d="M2 8c0-2 4.5-4 10-4s10 2 10 4v2h-5V8.5c-1.5-.4-3.2-.6-5-.6s-3.5.2-5 .6V10H2zM6 11h12l3 9H3zm4 2v1.5h1.5V13zm2.5 0v1.5H14V13zM10 15.5V17h1.5v-1.5zm2.5 0V17H14v-1.5z"/></svg>
        <span>0674 219 503</span>
      </li>
      <li class="contact-item">
        <svg class="contact-icon" viewBox="0 0 24 24" aria-hidden="true"><path d="M2 5h20v14H2zm3 3v8h2.5v-4.8L12 14.5l4.5-3.3V16H19V8h-1.5L12 12 6.5 8z"/></svg>
        <span>contact@verlindoillusions.example</span>
      </li>
      <li class="contact-item">
        <svg class="contact-icon" viewBox="0 0 24 24" aria-hidden="true"><path d="M12 2a10 10 0 1 0 0 20 10 10 0 0 0 0-20zm-1 17.9A8 8 0 0 1 4.2 10L9 14.8v1a2 2 0 0 0 2 2zm6.9-2.5a2 2 0 0 0-1.9-1.4h-1v-3a1 1 0 0 0-1-1H8v-2h2a1 1 0 0 0 1-1V7h2a2 2 0 0 0 2-2v-.4a8 8 0 0 1 2.9 12.8z"/></svg>
        <span>www.verlindoillusions.example</span>
      </li>
    </ul>
  </main>
</body>
</html>
```